High-end construction company needs a business card design

We need a modern looking business card that draws people in, is memorable and looks so good people will want to sick it on their fridges.
On the first side what is needed are:
Logo
My name - Tomasz Brelwik
Title - Managing Director
Website - www.varkelt.co.uk
Email - tomasz@varkelt.co.uk
Telephone - 020 5194 6281
Mobile - 07845139072
On the back side was is needed is a list of all the services we provide:
-Kitchen Renovations
-Bathroom Renovations
-House Renovations
-Garage Conversions
-Extensions
-Loft Conversions
-Conservatories
-Carpentry
-Tiling
-Electrical
-Plumbing & Heating
-Bricklaying
-Landscaping
-Decorating
-Plastering
We would like the colours to be the same shades as on the logo with grey or black for the words.
Target Market(s)
Anyone who needs building work done
Contact Information for Business Card
This business card is for a construction company which strives to deliver excellent service and quality.
The look and feel of the card should represent this.
Requirements
Must have
- On the first side what is needed are:
Logo
My name - Tomasz Brelwik
Title - Managing Director
Website - www.varkelt.co.uk
Email - tomasz@varkelt.co.uk
Telephone - 020 5194 6281
Mobile - 07845139072
Nice to have
- Cool looking features

```html
<!DOCTYPE html>
<html lang="en">
<head>
<meta charset="utf-8">
<title>Varkelt Construction Ltd – Business Card</title>
<link href="https://fonts.googleapis.com/css2?family=Open+Sans:wght@400;600;700&display=swap" rel="stylesheet">
<style>
  :root {
    --green-deep: #4a9339;
    --green-main: #5fa843;
    --green-light: #8cc63f;
    --green-bright: #6db644;
    --ink-grey: #555a5e;
    --paper: #ffffff;
    --backdrop: #e9ebec;
  }
  * { margin: 0; padding: 0; box-sizing: border-box; }
  html, body {
    width: 1200px; height: 1126px; overflow: hidden;
    background: var(--backdrop);
    font-family: "Open Sans", Arial, sans-serif;
  }
  .sheet {
    position: relative; width: 1200px; height: 1126px;
    display: flex; flex-direction: column; align-items: center;
    justify-content: space-evenly;
  }
  .card {
    position: relative; width: 900px; height: 515px; overflow: hidden;
    box-shadow: 0 6px 18px rgba(0,0,0,0.18);
  }

  /* Back: services */
  .card--back {
    background: linear-gradient(160deg, var(--green-main) 0%, var(--green-deep) 100%);
    color: var(--paper);
    text-align: center;
  }
  .brand {
    display: inline-flex; align-items: center; gap: 14px;
    font-weight: 700; letter-spacing: 0.06em; text-transform: uppercase;
  }
  .brand__mark { width: 18px; height: 18px; background: currentColor; }
  .card--back .brand {
    margin-top: 120px; font-size: 40px; color: var(--paper);
  }
  .services {
    list-style: none; margin-top: 92px;
    font-size: 21px; line-height: 1.55; font-weight: 400;
  }
  .services li span + span::before {
    content: "|"; color: var(--green-light); margin: 0 10px;
  }

  /* Front: contact */
  .card--front { background: var(--paper); }
  .card--front .brand {
    position: absolute; left: 52px; top: 70px;
    font-size: 30px; color: var(--green-bright);
  }
  .person { position: absolute; left: 52px; top: 196px; }
  .person__name { font-size: 30px; font-weight: 700; color: var(--green-bright); }
  .person__title { font-size: 22px; color: var(--ink-grey); margin-top: -2px; }
  .contact {
    position: absolute; left: 52px; top: 318px;
    list-style: none; font-size: 22px; color: var(--ink-grey); line-height: 31px;
  }
  .contact li { display: flex; align-items: center; gap: 12px; }
  .contact svg { width: 18px; height: 18px; fill: var(--green-bright); flex: none; }
  .contact .accent { color: var(--green-bright); }
  .hero-art {
    position: absolute; left: 360px; top: 200px; width: 540px; height: 315px;
    background: linear-gradient(135deg, var(--green-light) 0%, var(--green-main) 55%, var(--green-deep) 100%);
    clip-path: polygon(0 100%, 80% 8%, 92% 0, 100% 30%, 100% 100%);
  }
</style>
</head>
<body>
<main class="sheet">
  <section class="card card--back" aria-label="Back of card: services">
    <div class="brand"><span class="brand__mark"></span>Varkelt Construction Ltd</div>
    <ul class="services">
      <li><span>Kitchen Renovations</span><span>Bathroom Renovations</span><span>House Renovations</span></li>
      <li><span>Garage Conversions</span><span>Extensions</span><span>Loft Conversions</span><span>Conservatories</span></li>
      <li><span>Carpentry</span><span>Tiling</span><span>Electrical</span><span>Plumbing &amp; Heating</span><span>Bricklaying</span></li>
      <li><span>Landscaping</span><span>Decorating</span><span>Plastering</span></li>
    </ul>
  </section>

  <section class="card card--front" aria-label="Front of card: contact details">
    <div class="brand"><span class="brand__mark"></span>Varkelt Construction Ltd</div>
    <div class="person">
      <p class="person__name">Tomasz Brelwik</p>
      <p class="person__title">Managing Director</p>
    </div>
    <ul class="contact">
      <li><svg viewBox="0 0 24 24"><path d="M6.6 10.8a15 15 0 0 0 6.6 6.6l2.2-2.2a1 1 0 0 1 1-.25 11.4 11.4 0 0 0 3.6.57 1 1 0 0 1 1 1V20a1 1 0 0 1-1 1A17 17 0 0 1 3 4a1 1 0 0 1 1-1h3.5a1 1 0 0 1 1 1c0 1.25.2 2.45.57 3.6a1 1 0 0 1-.25 1z"/></svg>020 5194 6281</li>
      <li><svg viewBox="0 0 24 24"><path d="M7 1h10a2 2 0 0 1 2 2v18a2 2 0 0 1-2 2H7a2 2 0 0 1-2-2V3a2 2 0 0 1 2-2zm0 3v14h10V4zm5 15.2a1 1 0 1 0 0 2 1 1 0 0 0 0-2z"/></svg>07845139072</li>
      <li><svg viewBox="0 0 24 24"><path d="M2 5h20v14H2zm2 2v.4l8 5.2 8-5.2V7zm0 2.8V17h16V9.8l-8 5.2z"/></svg>tomasz@varkelt.co.uk</li>
      <li><svg viewBox="0 0 24 24"><path d="M12 2a10 10 0 1 0 0 20 10 10 0 0 0 0-20zm6.9 6h-3a15 15 0 0 0-1.3-4A8 8 0 0 1 18.9 8zM12 4c.8 1.2 1.5 2.5 1.9 4h-3.8c.4-1.5 1.1-2.8 1.9-4zM4.3 14a8 8 0 0 1 0-4h3.4a16 16 0 0 0 0 4zm.8 2h3a15 15 0 0 0 1.3 4A8 8 0 0 1 5.1 16zm3-8h-3a8 8 0 0 1 4.3-4A15 15 0 0 0 8.1 8zM12 20c-.8-1.2-1.5-2.5-1.9-4h3.8c-.4 1.5-1.1 2.8-1.9 4zm2.3-6H9.7a14 14 0 0 1 0-4h4.6a14 14 0 0 1 0 4zm.3 6a15 15 0 0 0 1.3-4h3a8 8 0 0 1-4.3 4zm1.7-6a16 16 0 0 0 0-4h3.4a8 8 0 0 1 0 4z"/></svg>www.<span class="accent">varkelt</span>.co.uk</li>
    </ul>
    <div class="hero-art" role="img" aria-label="Green illustration of an excavator arm reaching over a house roof and city buildings"></div>
  </section>
</main>
</body>
</html>
```